Zielgruppe
Verkauf und Einbau von Fenstern, Haustüren, Rollläden, Raffstore, Markisen, Insektenschutzgitter, Plissees
Aufgabenstellung
Es soll das gleiche Farbschema meines Firmenlogos haben. Grauer Hintergrund, kleine gelbe Akzente und schwarze Schrift

```html
<!DOCTYPE html>
<html lang="de">
<head>
<meta charset="utf-8">
<title>Rahmenwerk – Webseite</title>
<link href="https://fonts.googleapis.com/css2?family=Montserrat:wght@400;500;600;700&display=swap" rel="stylesheet">
<style>
:root{
  --stage:#e4e4e4;
  --page:#f2f2f2;
  --white:#ffffff;
  --brown:#5b3a25;
  --brown-dark:#3a2416;
  --brown-text:#6a2e12;
  --ink:#2a1a10;
  --yellow:#f0bf17;
  --yellow-deep:#d9a80e;
  --grey-text:#5d5d5d;
}
*{box-sizing:border-box;margin:0;padding:0}
html,body{width:1200px;height:1200px;overflow:hidden}
body{background:var(--stage);font-family:"Montserrat",sans-serif;color:var(--ink);position:relative}
.abs{position:absolute}
.photo{position:absolute}

/* ---------- full page layout ---------- */
.page{position:absolute;left:62px;top:20px;width:409px;height:1153px;background:var(--page);overflow:hidden}

.hero{position:absolute;left:0;top:0;width:409px;height:230px;
  background:radial-gradient(ellipse at 40% 45%,#8a6a4c 0%,#5e4330 45%,#3b2a1e 100%)}
.hero .nav{position:absolute;left:0;top:0;width:100%;height:26px;background:rgba(80,50,30,.85);
  display:flex;align-items:center;font-size:5.6px;color:var(--white);font-weight:500}
.nav span{position:absolute}
.nav .active{text-decoration:underline}
.brand-name{font-weight:500;color:var(--yellow);letter-spacing:.02em;white-space:nowrap}
.brand-tag{font-weight:500;color:var(--white);white-space:nowrap;letter-spacing:.02em}
.center{text-align:center;left:0;width:100%}
.btn-yellow{position:absolute;background:var(--yellow-deep);color:var(--white);font-weight:600;
  display:flex;align-items:center;justify-content:center}
.social{position:absolute;border:1px solid var(--white);border-radius:50%;color:var(--white);
  display:flex;align-items:center;justify-content:center;font-weight:500}

.section-title{position:absolute;font-weight:600;letter-spacing:.16em;color:var(--brown-dark);text-transform:uppercase;line-height:1.3}
.small-text{position:absolute;font-size:3.8px;line-height:1.7;color:var(--grey-text)}

.card{position:absolute;top:283px;width:103px;height:154px;background:var(--white);box-shadow:0 1px 3px rgba(0,0,0,.18)}
.card .photo{left:0;top:0;width:103px;height:65px}
.card h3{position:absolute;left:13px;top:74px;font-size:8.6px;font-weight:500;color:var(--brown-text);line-height:1.15}
.card p{position:absolute;left:13px;top:101px;width:80px;font-size:2.9px;line-height:1.75;color:var(--grey-text)}
.card .more{position:absolute;left:13px;top:130px;width:53px;height:11px;border:1px solid var(--brown-text);
  font-size:4.3px;font-weight:700;color:var(--brown-text);display:flex;align-items:center;justify-content:center}
.arrow{position:absolute;top:343px;width:13px;height:13px;border-radius:50%;background:var(--white);
  box-shadow:0 0 2px rgba(0,0,0,.3)}
.dots{position:absolute;top:445px;left:205px;display:flex;gap:2px}
.dots i{width:4px;height:4px;border-radius:50%;border:.8px solid var(--ink)}
.dots i.on{background:var(--ink)}

.divider{position:absolute;left:0;top:691px;width:100%;height:1px;background:#dcdcdc}
.team-mark{position:absolute;left:270px;width:139px;text-align:center;z-index:2}
.badge{position:absolute;left:275px;top:860px;width:50px;height:50px;border-radius:50%;background:var(--yellow-deep);
  color:var(--white);font-size:5.2px;font-weight:600;text-align:center;display:flex;flex-direction:column;justify-content:center;line-height:1.15;z-index:3}
.field{position:absolute;background:var(--yellow-deep);opacity:.9;color:var(--white);font-size:5px;font-weight:600;padding-left:13px;display:flex;align-items:center}
.field.tall{align-items:flex-start;padding-top:7px}
.btn-outline{position:absolute;border:1px solid var(--white);color:var(--white);font-size:5.2px;font-weight:700;display:flex;align-items:center;justify-content:center}
.hours{position:absolute;font-size:3.8px;line-height:1.6;color:var(--grey-text)}
.hours td{padding-right:4px;vertical-align:top}

/* ---------- brand block ---------- */
.brand-block{position:absolute;left:640px;top:222px;width:400px;text-align:center}
.brand-block .name{font-size:46px;font-weight:500;color:var(--yellow);letter-spacing:.04em;line-height:1.1}
.brand-block .tag{margin-top:6px;font-size:15px;font-weight:600;color:var(--ink);letter-spacing:.03em}

/* ---------- large hero ---------- */
.hero-lg{position:absolute;left:530px;top:422px;width:615px;height:348px;
  background:radial-gradient(ellipse at 45% 45%,#8a6a4c 0%,#5e4330 45%,#3b2a1e 100%);color:var(--white)}
.hero-lg .nav{position:absolute;left:0;top:0;width:100%;height:38px;background:rgba(80,50,30,.85);font-size:8.6px;font-weight:500}
.hero-lg .nav span{position:absolute;top:15px}
</style>
</head>
<body>

<!-- ================= FULL PAGE ================= -->
<div class="page">

  <section class="hero" role="img" aria-label="Foto: Hände hobeln ein Holzbrett, Hobelspäne ringsum">
    <div class="nav">
      <span class="active" style="left:22px">Startseite</span>
      <span style="left:67px">Produkte</span>
      <span style="left:118px">Abgeschlossene Projekte</span>
      <span style="left:204px">Wer wir sind</span>
      <span style="left:357px">Kontakt</span>
    </div>
    <div class="abs center brand-name" style="top:110px;font-size:15px">RAHMENWERK</div>
    <div class="abs center brand-tag" style="top:130px;font-size:5.4px">FENSTER HAUSTÜREN SONNENSCHUTZ</div>
    <div class="abs center" style="top:147px;font-size:5.2px;font-weight:700;letter-spacing:.2em">WILLKOMMEN</div>
    <div class="abs center" style="top:161px;font-size:4.6px;font-weight:600;letter-spacing:.06em;line-height:1.4">Verkauf und Einbau von Fenstern, Haustüren, Rollläden,<br>Raffstore, Markisen, Insektenschutzgitter, Plissees</div>
    <div class="btn-yellow" style="left:178px;top:184px;width:52px;height:14px;font-size:4.6px">Kontaktieren</div>
    <div class="social" style="left:21px;top:201px;width:12px;height:12px;font-size:2.8px">Social</div>
    <span class="abs" style="left:318px;top:215px;font-size:4.4px;color:#fff">Impressum</span>
    <span class="abs" style="left:360px;top:215px;font-size:4.4px;color:#fff">Datenschutz</span>
  </section>

  <section class="products">
    <div class="section-title center" style="top:249px;font-size:9.4px;text-align:center">Alle Produkte im Überblick</div>
    <div class="abs center" style="top:262px;font-size:5.6px;letter-spacing:.05em;color:var(--ink);font-weight:500">Klicken Sie sich durch unser breites Sortiment.</div>

    <div class="arrow" style="left:14px"><svg width="13" height="13" viewBox="0 0 13 13"><path d="M7.8 4 L4.8 6.5 L7.8 9" fill="none" stroke="#777" stroke-width="1"/></svg></div>
    <div class="arrow" style="left:382px"><svg width="13" height="13" viewBox="0 0 13 13"><path d="M5.2 4 L8.2 6.5 L5.2 9" fill="none" stroke="#777" stroke-width="1"/></svg></div>

    <article class="card" style="left:36px">
      <div class="photo" role="img" aria-label="Foto: Handwerker mit Helm montiert ein Fenster" style="background:linear-gradient(90deg,#7a6a5c,#c9c6c2 60%,#e8e8e8)"></div>
      <h3>Einbau<br>von Fenstern</h3>
      <p>Wir messen exakt, beraten ehrlich und montieren sauber. Saubere Arbeit vom Aufmaß bis zur Abnahme beim Kunden vor Ort.</p>
      <div class="more">Mehr erfahren</div>
    </article>
    <article class="card" style="left:153px">
      <div class="photo" role="img" aria-label="Foto: Hauseingang mit brauner Holzhaustür" style="background:linear-gradient(90deg,#8d8d8a,#6b3a22 45%,#9a9a95 70%,#d0d0cc)"></div>
      <h3>Einbau<br>von Haustüren</h3>
      <p>Wir messen exakt, beraten ehrlich und montieren sauber. Saubere Arbeit vom Aufmaß bis zur Abnahme beim Kunden vor Ort.</p>
      <div class="more">Mehr erfahren</div>
    </article>
    <article class="card" style="left:269px">
      <div class="photo" role="img" aria-label="Foto: Mann am Telefon vor einem Fenster mit Rollo" style="background:linear-gradient(90deg,#f3f1ee,#9aa3b3 35%,#ebe7e1 60%,#f5f3ef)"></div>
      <h3>Einbau<br>von Rolläden</h3>
      <p>Wir messen exakt, beraten ehrlich und montieren sauber. Saubere Arbeit vom Aufmaß bis zur Abnahme beim Kunden vor Ort.</p>
      <div class="more">Mehr erfahren</div>
    </article>
    <div class="dots"><i class="on"></i><i></i><i></i></div>
  </section>

  <section class="projects">
    <div class="section-title" style="left:27px;top:487px;font-size:9.4px">Unsere<br>abgeschlossenen Projekte</div>
    <p class="small-text" style="left:27px;top:517px;width:140px">Ein Auszug aus unseren Arbeiten der letzten Jahre: neue Fenster, moderne Haustüren und passender Sonnenschutz für Häuser in der Region.</p>
    <div class="photo" role="img" aria-label="Foto: schwarze Haustür neben Klinkerwand" style="left:261px;top:474px;width:128px;height:86px;background:linear-gradient(90deg,#4a4a48,#1f1f1f 35%,#6e5a4a 55%,#b59a80)"></div>
    <div class="photo" role="img" aria-label="Foto: Hand öffnet helle Vertikaljalousie" style="left:27px;top:555px;width:120px;height:95px;background:linear-gradient(90deg,#f2eee4,#e1d8c6 60%,#9c8c72)"></div>
    <div class="photo" role="img" aria-label="Foto: heller Wohnraum mit großen Fenstern und Pflanzen" style="left:172px;top:539px;width:113px;height:74px;background:linear-gradient(90deg,#e8e8e4,#c9cfc3 50%,#9c8c72)"></div>
    <div class="photo" role="img" aria-label="Foto: Frau an bodentiefem Fenster mit Stadtblick" style="left:126px;top:593px;width:77px;height:89px;background:linear-gradient(180deg,#8c8778,#c2b9a4 50%,#6f6658)"></div>
    <div class="photo" role="img" aria-label="Foto: Frau sitzt auf Fensterbank eines Sprossenfensters" style="left:226px;top:576px;width:165px;height:94px;background:linear-gradient(90deg,#e4e4e2,#cfcfcc 60%,#8a8f92)"></div>
  </section>

  <div class="divider"></div>

  <section class="about">
    <div class="photo" role="img" aria-label="Foto: Holzrohbau mit Balken" style="left:244px;top:692px;width:165px;height:230px;background:linear-gradient(180deg,#7a4a26,#a8723e 50%,#5e3a1e)"></div>
    <div class="photo" role="img" aria-label="Foto: lächelnder Handwerker in Latzhose mit verschränkten Armen" style="left:182px;top:722px;width:92px;height:200px;background:linear-gradient(180deg,#b48a6c 0%,#8a8a86 35%,#2e3a4e 60%,#263246)"></div>
    <div class="team-mark brand-name" style="top:768px;font-size:10px">RAHMENWERK</div>
    <div class="team-mark brand-tag" style="top:781px;font-size:3.6px">FENSTER HAUSTÜREN SONNENSCHUTZ</div>
    <div class="badge">Werde Teil<br>des Teams.<br>Bewirb dich!</div>

    <div class="section-title" style="left:27px;top:723px;font-size:9.4px">Wer wir sind?<br>Blicken Sie hinter<br>die Fassade.</div>
    <p class="small-text" style="left:28px;top:770px;width:140px">Ein kleines Team aus Handwerkern mit viel Erfahrung und Freude am Holz.</p>
    <div class="abs" style="left:28px;top:792px;font-size:5.6px;font-weight:600;color:var(--brown-text)">Lorem ipsum</div>
    <p class="small-text" style="left:28px;top:801px;width:140px">Seit vielen Jahren planen und montieren wir Fenster, Türen und Sonnenschutz. Jeder Auftrag wird von einem festen Ansprechpartner begleitet, vom ersten Gespräch bis zur fertigen Montage.</p>
    <p class="small-text" style="left:28px;top:840px;width:140px">Wir arbeiten mit geprüften Herstellern und achten auf gute Dämmung, sichere Beschläge und lange Haltbarkeit. Nach dem Einbau bleiben wir für Wartung und Fragen gern für Sie da.</p>
  </section>

  <section class="contact">
    <div class="photo" role="img" aria-label="Foto: Hände an einer Tastatur in warmem Licht" style="left:0;top:922px;width:202px;height:231px;background:linear-gradient(135deg,#6a4a22,#a7781c 45%,#3e2c18)"></div>
    <div class="field" style="left:33px;top:962px;width:64px;height:12px">Name</div>
    <div class="field" style="left:107px;top:962px;width:61px;height:12px">Vorname</div>
    <div class="field" style="left:33px;top:985px;width:135px;height:12px">E-Mail Adresse</div>
    <div class="field" style="left:33px;top:1004px;width:135px;height:12px">Telefonnummer</div>
    <div class="field tall" style="left:33px;top:1027px;width:135px;height:71px">Ihre Nachricht ...</div>
    <div class="btn-outline" style="left:33px;top:1108px;width:65px;height:13px">Kontaktieren</div>

    <div class="section-title" style="left:226px;top:977px;font-size:9.4px">Kontaktieren Sie uns.<br>Wir freuen uns auf<br>Ihre Anfrage.</div>
    <p class="small-text" style="left:228px;top:1027px;width:150px">Schreiben Sie uns oder rufen Sie an. Wir melden uns schnell mit einem Termin für die Beratung.</p>
    <table class="hours" style="left:228px;top:1052px;border-collapse:collapse">
      <tr><td colspan="2">Öffnungszeiten:</td></tr>
      <tr><td>Dienstag - Freitag:</td><td>17-23 Uhr</td></tr>
      <tr><td>Samstag:</td><td>17-0 Uhr</td></tr>
      <tr><td>Sonntag:</td><td>17 - 22 Uhr</td></tr>
      <tr><td>Montag:</td><td>Ruhetag</td></tr>
    </table>
    <div class="hours" style="left:320px;top:1052px">Hier findest du uns:<br><br style="line-height:.6">Grüner Anker Café<br>Lindenweg 12<br>04109 Talheim</div>
    <div class="hours" style="left:228px;top:1093px;display:flex;align-items:center;gap:2px">
      <svg width="5" height="5" viewBox="0 0 10 10"><path d="M2 1 L4 1 L5 3.5 L3.6 4.6 Q4.6 6.4 5.6 6.6 L6.6 5.2 L9 6.2 L9 8.4 Q8.6 9.2 7.4 9 Q1.4 7.6 1 2.4 Q1 1.2 2 1Z" fill="none" stroke="#5d5d5d" stroke-width=".9"/></svg>0151 23 45 678</div>
    <div class="hours" style="left:228px;top:1101px;display:flex;align-items:center;gap:2px">
      <svg width="5" height="4" viewBox="0 0 10 8"><rect x=".5" y=".5" width="9" height="7" fill="none" stroke="#5d5d5d"/><path d="M.5 .5 L5 4.5 L9.5 .5" fill="none" stroke="#5d5d5d"/></svg>info@gruener-anker.de</div>
  </section>
</div>

<!-- ================= BRAND BLOCK ================= -->
<div class="brand-block">
  <div class="name">RAHMENWERK</div>
  <div class="tag">FENSTER HAUSTÜREN SONNENSCHUTZ</div>
</div>

<!-- ================= LARGE HERO ================= -->
<section class="hero-lg" role="img" aria-label="Foto: Hände hobeln ein Holzbrett, Hobelspäne ringsum">
  <div class="nav">
    <span style="left:33px;text-decoration:underline">Startseite</span>
    <span style="left:102px">Produkte</span>
    <span style="left:178px">Abgeschlossene Projekte</span>
    <span style="left:308px">Wer wir sind</span>
    <span style="left:540px">Kontakt</span>
  </div>
  <div class="abs center brand-name" style="top:124px;font-size:26px">RAHMENWERK</div>
  <div class="abs center brand-tag" style="top:157px;font-size:9px">FENSTER HAUSTÜREN SONNENSCHUTZ</div>
  <div class="abs center" style="top:190px;font-size:8.4px;font-weight:700;letter-spacing:.2em">WILLKOMMEN</div>
  <div class="abs center" style="top:208px;font-size:7.8px;font-weight:600;letter-spacing:.06em;line-height:1.3">Verkauf und Einbau von Fenstern, Haustüren, Rollläden,<br>Raffstore, Markisen, Insektenschutzgitter, Plissees</div>
  <div class="btn-yellow" style="left:268px;top:278px;width:78px;height:21px;font-size:7.4px">Kontaktieren</div>
  <div class="social" style="left:30px;top:304px;width:17px;height:17px;font-size:3.8px">Social</div>
  <span class="abs" style="left:480px;top:330px;font-size:7px">Impressum</span>
  <span class="abs" style="left:545px;top:330px;font-size:7px">Datenschutz</span>
</section>

</body>
</html>
```